Recruitment Site Design

We need a design for the login page, about page, and inner pages of a recruitment site for an oil and gas company. Design should be modern, sleek, professional and colors can be blue, green, white, orange or any other recommended colors.

Please also take into consideration that once the users login, they will need to access a form to fill in their information.

** UPDATE: Kindly provide a design for the inner information page consistent with the outer design. Attached is a picture of the basic structure. ***
Updates

Please provide a design for inner pages as shown in the design brief consistent with the registration page provided. 

Reason: We're extending it to get more inside pages.

Target Market(s)

Professionals looking for a career in the oil and gas industry in the Middle East.

Industry/Entity Type

Oil And Gas

Requirements
Must have
• Sleek design

```html
<!DOCTYPE html>
<html lang="en">
<head>
<meta charset="utf-8">
<title>Recruitment Login</title>
<link rel="stylesheet" href="https://fonts.googleapis.com/css2?family=Ropa+Sans&display=swap">
<style>
:root{
  --orange:#e0861c;
  --orange-dark:#c0651a;
  --band:#c07428;
  --band-edge:#8f531b;
  --nav-text:#454545;
  --panel:#ececee;
  --field-text:#555;
  --white:#ffffff;
  --sky-top:#4f7fbf;
  --sky-mid:#a9c3e2;
  --ground:#6f8a4a;
}
*{box-sizing:border-box;margin:0;padding:0}
html,body{width:1200px;height:768px;overflow:hidden}
body{position:relative;font-family:"Ropa Sans",Arial,sans-serif;background:var(--band)}
.hero{position:absolute;left:0;top:0;width:1200px;height:576px;
  background:linear-gradient(180deg,var(--sky-top) 0%,var(--sky-mid) 45%,#d7e2ee 70%,#8f9a7a 88%,var(--ground) 100%)}
.header-bar{position:absolute;left:0;top:37px;width:1200px;height:67px;background:rgba(236,237,240,.93)}
.logo-box{position:absolute;left:185px;top:19px;width:163px;height:104px;border:3px solid #f7f7f7;border-radius:8px;
  background:#e9e9eb;box-shadow:0 1px 4px rgba(0,0,0,.25);display:flex;align-items:center;justify-content:center}
.logo-box span{font-size:60px;color:var(--orange-dark);line-height:1}
.main-nav{position:absolute;top:37px;left:0;height:67px;list-style:none}
.main-nav li{position:absolute;top:20px;font-size:15px;letter-spacing:.3px;color:var(--nav-text);line-height:28px;white-space:nowrap}
.main-nav li.sep{width:1px;height:28px;background:#c9c9cc}
.nav-home{left:507px;color:var(--orange) !important}
.nav-about{left:607px}
.nav-find{left:720px}
.nav-register{left:832px}
.nav-contact{left:976px}
.login-panel{position:absolute;left:474px;top:144px;width:260px;height:368px;background:rgba(238,238,240,.96);
  border-radius:10px;box-shadow:0 2px 8px rgba(0,0,0,.3)}
.tab{position:absolute;display:block}
.tab svg{position:absolute;left:0;top:0}
.tab-label{position:absolute;left:0;width:100%;text-align:center;color:var(--white);font-size:18px;letter-spacing:.3px;text-shadow:0 1px 1px rgba(0,0,0,.35)}
.tab-top{left:44px;top:-1px;width:172px;height:70px}
.tab-top .tab-label{top:29px}
.tab-bottom{left:24px;top:296px;width:212px;height:72px}
.tab-bottom .tab-label{top:30px}
.field{position:absolute;left:24px;width:211px;height:41px;background:var(--white);border:1px solid #dcdcdf;border-radius:6px;
  padding-left:9px;font-size:15px;color:var(--field-text);line-height:39px}
.field-user{top:94px}
.field-pass{top:144px}
.btn-login{position:absolute;left:79px;top:195px;width:102px;height:40px;border-radius:4px;
  background:linear-gradient(180deg,#ec9a2a,#d9780f);color:var(--white);font-size:17px;text-align:center;line-height:40px;
  box-shadow:0 1px 2px rgba(0,0,0,.3)}
.member-note{position:absolute;left:0;top:261px;width:100%;text-align:center;font-size:15px;color:#444}
.slider-tab{position:absolute;left:543px;top:540px;width:110px;height:38px}
.info-band{position:absolute;left:0;top:575px;width:1200px;height:193px;background:var(--band);border-top:4px solid var(--band-edge)}
.welcome-title{position:absolute;left:174px;top:590px;font-size:21px;color:var(--white);font-weight:400;letter-spacing:.3px;text-shadow:0 1px 1px rgba(0,0,0,.3)}
.title-rule{position:absolute;left:174px;top:622px;width:842px;height:1px;background:rgba(255,255,255,.45)}
.welcome-text{position:absolute;left:174px;top:631px;width:848px;font-size:13.6px;letter-spacing:.55px;line-height:20px;color:#fbeee0}
.footer-note{position:absolute;left:0;top:727px;width:1238px;text-align:center;font-size:13.5px;line-height:16px;color:#fbeee0}
.footer-note u{text-decoration:underline}
.social{position:absolute;top:735px;width:16px;height:16px;background:#e9d7c2;border-radius:2px}
.social-a{left:863px}
.social-b{left:883px}
</style>
</head>
<body>
<div class="hero" role="img" aria-label="Photo of an oil field with pump jacks under a cloudy blue sky and an engineer in orange coveralls holding a laptop"></div>
<div class="header-bar"></div>
<div class="logo-box"><span>Logo</span></div>
<ul class="main-nav">
  <li class="nav-home">Home</li>
  <li class="sep" style="left:577px"></li>
  <li class="nav-about">About Us</li>
  <li class="sep" style="left:692px"></li>
  <li class="nav-find">Find Job</li>
  <li class="sep" style="left:804px"></li>
  <li class="nav-register">Register Here</li>
  <li class="sep" style="left:946px"></li>
  <li class="nav-contact">Contact Us</li>
</ul>

<div class="login-panel">
  <div class="tab tab-top">
    <svg width="172" height="70" viewBox="0 0 172 70">
      <defs><linearGradient id="tabGrad" x1="0" y1="0" x2="0" y2="1">
        <stop offset="0" stop-color="#f3a637"/><stop offset="1" stop-color="#c9620f"/></linearGradient></defs>
      <path d="M0 0 H172 L152 58 Q148 68 136 68 H36 Q24 68 20 58 Z" fill="#f7f7f7"/>
      <path d="M6 0 H166 L148 55 Q145 64 134 64 H38 Q27 64 24 55 Z" fill="url(#tabGrad)"/>
    </svg>
    <span class="tab-label">Login Now</span>
  </div>
  <div class="field field-user">User Name</div>
  <div class="field field-pass">Password</div>
  <div class="btn-login">Login</div>
  <p class="member-note">Not a Member?</p>
  <div class="tab tab-bottom">
    <svg width="212" height="72" viewBox="0 0 212 72">
      <defs><linearGradient id="tabGrad2" x1="0" y1="0" x2="0" y2="1">
        <stop offset="0" stop-color="#f3a637"/><stop offset="1" stop-color="#c9620f"/></linearGradient></defs>
      <path d="M0 72 L26 12 Q30 2 42 2 H170 Q182 2 186 12 L212 72 Z" fill="#f7f7f7"/>
      <path d="M8 72 L32 16 Q36 7 46 7 H166 Q176 7 180 16 L204 72 Z" fill="url(#tabGrad2)"/>
    </svg>
    <span class="tab-label">Register Here</span>
  </div>
</div>

<svg class="slider-tab" viewBox="0 0 110 38">
  <defs><linearGradient id="sliderGrad" x1="0" y1="0" x2="0" y2="1">
    <stop offset="0" stop-color="#f0a23a"/><stop offset="1" stop-color="#c9701e"/></linearGradient></defs>
  <path d="M0 38 L12 8 Q15 1 24 1 H86 Q95 1 98 8 L110 38 Z" fill="url(#sliderGrad)"/>
  <circle cx="33" cy="18" r="6" fill="#7a4a12"/><circle cx="33" cy="18" r="4" fill="#d9a020"/>
  <circle cx="56" cy="18" r="6" fill="#e9e9ee"/>
  <circle cx="78" cy="18" r="6" fill="#e9e9ee"/>
</svg>

<section class="info-band"></section>
<h1 class="welcome-title">Welcome to our site</h1>
<div class="title-rule"></div>
<p class="welcome-text">We need a design for the login page, about page, and inner pages of a recruitment site for an oil and gas company. Design should be modern, sleek, professional and colors can be blue, green, white, orange or any other recommended colors. We need a design for the login page, about page, and inner pages of a recruitment site for an oil and gas company. Design should be modern, sleek, professional and colors can be blue, green, white, orange or any other recommended colors. We need a design for the login page, about page, and inner pages of a recruitment site for us.</p>
<p class="footer-note">Copyright @ 2012, <u>Company Name</u><br>Terms &amp; Privacy Policy</p>
<span class="social social-a"></span>
<span class="social social-b"></span>
</body>
</html>
```